High end Electrical/home automation Business Card

Need a card for a high end electrical and home automation company utilising the existing logo.
Phone
Email
Website

Like black look with raised detail. Don’t necessarily need to keep colour of logo it could be made grayscale or white etc

Target Market(s)

High end clients

Contact Information for Business Card

Brightmoor Electrical

Requirements
Must have
• Logo, phone, email, website, address

High end look
Nice to have
• Black background card
Raised font
Should not have
• Lots of colour

```html
<!DOCTYPE html>
<html lang="en">
<head>
<meta charset="utf-8">
<title>Brightmoor Electrical – Business Card</title>
<link href="https://fonts.googleapis.com/css2?family=Work+Sans:wght@400;500;700;800&display=swap" rel="stylesheet">
<style>
  :root {
    --charcoal: #38383a;
    --paper: #ffffff;
    --blue: #0a8fd8;
    --ink: #2e2e30;
    --backdrop: #e9e9ea;
  }
  * { box-sizing: border-box; margin: 0; padding: 0; }
  html, body { width: 1200px; height: 881px; overflow: hidden; }
  body {
    background: var(--backdrop);
    font-family: "Work Sans", Arial, sans-serif;
    position: relative;
  }
  .card {
    position: absolute;
    left: 300px;
    width: 600px;
    height: 343px;
    overflow: hidden;
    box-shadow: 0 6px 18px rgba(0,0,0,.18);
  }

  /* Front */
  .card-front { top: 80px; background: var(--charcoal); }
  .front-brand {
    position: absolute;
    left: 0; right: 0; top: 110px;
    text-align: center;
  }
  .brand-dot {
    display: block;
    width: 64px; height: 64px;
    margin: 0 auto 18px;
    border-radius: 50%;
    border: 8px solid var(--blue);
  }
  .front-name {
    color: var(--paper);
    font-weight: 800;
    font-size: 34px;
    letter-spacing: -0.5px;
  }

  /* Back */
  .card-back { top: 463px; background: var(--paper); }
  .back-band {
    position: absolute; inset: 0;
  }
  .back-name {
    position: absolute;
    left: 30px; top: 26px;
    color: var(--ink);
    font-weight: 800;
    font-size: 44px;
    letter-spacing: -1px;
    white-space: nowrap;
  }
  .accent-bar {
    position: absolute;
    left: 0; top: 118px;
    width: 8px; height: 42px;
    background: var(--blue);
  }
  .person { position: absolute; left: 30px; top: 114px; }
  .person-name {
    color: var(--blue);
    font-weight: 500;
    font-size: 19px;
    letter-spacing: 2.5px;
    text-transform: uppercase;
  }
  .person-role { color: var(--ink); font-size: 15px; letter-spacing: 1px; margin-top: 2px; }
  .contact {
    position: absolute;
    left: 30px; top: 222px;
    color: var(--paper);
    font-size: 14px;
    letter-spacing: 1px;
    line-height: 1.35;
    list-style: none;
  }
  .contact li { display: flex; align-items: center; gap: 8px; }
  .contact .address { margin-bottom: 6px; display: block; }
  .contact svg { width: 12px; height: 12px; flex: none; }
  .back-mark {
    position: absolute;
    right: 34px; top: 104px;
    width: 116px; height: 116px;
    border-radius: 50%;
    border: 14px solid var(--blue);
    background: transparent;
  }
</style>
</head>
<body>
  <section class="card card-front" aria-label="Card front">
    <div class="front-brand">
      <span class="brand-dot" aria-hidden="true"></span>
      <div class="front-name">Brightmoor Electrical</div>
    </div>
  </section>

  <section class="card card-back" aria-label="Card back">
    <svg class="back-band" viewBox="0 0 600 343" preserveAspectRatio="none" aria-hidden="true">
      <polygon points="0,210 380,210 380,130 600,130 600,343 0,343" fill="var(--charcoal)"/>
    </svg>
    <div class="back-name">Brightmoor Electrical</div>
    <span class="accent-bar" aria-hidden="true"></span>
    <div class="person">
      <div class="person-name">Daniel Reyes</div>
      <div class="person-role">Founder</div>
    </div>
    <ul class="contact">
      <li class="address">418 Larch Avenue<br>Colville, WA 99114</li>
      <li>
        <svg viewBox="0 0 12 12" aria-hidden="true"><path d="M3 1 L5 3.5 L3.8 5 Q5 7.5 7 8.2 L8.5 7 L11 9 L9.5 11 Q4 10.5 1 3 Z" fill="none" stroke="currentColor" stroke-width="1"/></svg>
        555 014 2273
      </li>
      <li>
        <svg viewBox="0 0 12 12" aria-hidden="true"><rect x="1" y="2.5" width="10" height="7" fill="none" stroke="currentColor" stroke-width="1"/><path d="M1 2.5 L6 6.5 L11 2.5" fill="none" stroke="currentColor" stroke-width="1"/></svg>
        hello@brightmoorelectrical.com
      </li>
      <li>
        <svg viewBox="0 0 12 12" aria-hidden="true"><circle cx="6" cy="6" r="5" fill="none" stroke="currentColor" stroke-width="1"/><ellipse cx="6" cy="6" rx="2.2" ry="5" fill="none" stroke="currentColor" stroke-width="1"/><path d="M1 6 H11" stroke="currentColor" stroke-width="1"/></svg>
        brightmoorelectrical.com
      </li>
    </ul>
    <span class="back-mark" aria-hidden="true"></span>
  </section>
</body>
</html>
```